Business Card Design for BrightvaleMedia.com

--I need a business card design for my company BrightvaleMedia.com

I have attached my logo...I want the brightvale media logo on the front of the business card, and then I want The Quillstone Chief on the back of it with my information.

I would like to see a light colored background as well as a dark colored background

FRONT:
BRIGHTVALE MEDIA LOGO
248 N. Larkmoor
3rd Floor
San Diego CA 92173
www.BrightvaleMedia.com

Advanced Website & App Development
Websites, Apps, Online Voucher Systems

Leading Edge Marketing Services
SMS, VB, SMM, SEM,

BACK:
QUILLSTONE CHIEF LOGO
Dorian Pelletta
The Quillstone Chief
Call Or Text: 619-555-0148
Dorian@QuillstoneChief.example
www.QuillstoneChief.example

Target Market(s)

small business owners

Industry/Entity Type

Business Consultant

Contact Information for Business Card

FRONT:
BRIGHTVALE MEDIA LOGO
248 N. Larkmoor
3rd Floor
San Diego CA 92173
www.BrightvaleMedia.com

SMS, VB, SMM, SEM,

BACK:
QUILLSTONE CHIEF LOGO
Dorian Pelletta
The Quillstone Chief
Dorian@QuillstoneChief.example
www.QuillstoneChief.example

Requirements
Must have
• add this quote on it somewhere, anywhere,preferrably on back
• "The Fastest Way To Success Is To Take Action”
• — Dorian Pelletta, Quillstone Chief
Nice to have
• open
Should not have
• red

```html
<!DOCTYPE html>
<html lang="en">
<head>
<meta charset="utf-8">
<title>Brightvale Media — Business Cards</title>
<link rel="stylesheet" href="https://fonts.googleapis.com/css2?family=Lato:ital,wght@0,400;0,700;1,400&display=swap">
<style>
  :root {
    --backdrop: #1c1c1c;
    --brand-blue: #0e72ad;
    --card-white: #ffffff;
    --ink-dark: #2b2b2b;
    --ink-muted: #5a5a5a;
    --ink-light: #ffffff;
  }
  * { margin: 0; padding: 0; box-sizing: border-box; }
  html, body {
    width: 1200px; height: 900px; overflow: hidden;
    background: var(--backdrop);
    font-family: "Lato", sans-serif;
  }
  .stage { position: relative; width: 1200px; height: 900px; }

  .card {
    position: absolute; top: 170px;
    width: 347px; height: 561px;
    text-align: center;
  }
  .card--personal { left: 259px; background: var(--card-white); color: var(--ink-dark); }
  .card--company { left: 631px; background: var(--brand-blue); color: var(--ink-light); }

  .accent-band {
    position: absolute; left: 91px;
    width: 165px; background: var(--brand-blue);
  }
  .accent-band--top { top: 0; height: 30px; }
  .accent-band--bottom { bottom: 0; height: 28px; }

  .wordmark {
    position: absolute; left: 0; right: 0;
    font-weight: 700; letter-spacing: 2px; white-space: nowrap;
  }
  .card--personal .wordmark { top: 152px; font-size: 25px; color: var(--brand-blue); }
  .card--company .wordmark { top: 138px; font-size: 25px; color: var(--ink-light); }

  .quote {
    position: absolute; left: 34px; right: 34px; top: 228px;
    color: var(--ink-muted);
  }
  .quote__text { font-size: 13px; font-style: italic; line-height: 18px; }
  .quote__author { margin-top: 4px; font-size: 11px; line-height: 14px; }

  .holder { position: absolute; left: 0; right: 0; top: 323px; }
  .holder__name {
    font-size: 20px; font-weight: 700; letter-spacing: 1.5px;
    color: var(--brand-blue); text-transform: uppercase; line-height: 24px;
  }
  .holder__title { font-size: 15px; line-height: 20px; }

  .contact { position: absolute; left: 0; right: 0; top: 403px; font-size: 15px; line-height: 20px; }
  .contact__icons { display: flex; justify-content: center; gap: 6px; margin-bottom: 3px; }
  .contact__icons svg { width: 15px; height: 15px; fill: var(--brand-blue); }

  .services { position: absolute; left: 0; right: 0; top: 284px; font-size: 15.5px; line-height: 20px; }
  .services__group + .services__group { margin-top: 14px; }
  .address { position: absolute; left: 0; right: 0; top: 424px; font-size: 15.5px; line-height: 20px; }
  .address__web { margin-top: 13px; }
</style>
</head>
<body>
<main class="stage">
  <section class="card card--personal" aria-label="Personal card">
    <div class="accent-band accent-band--top"></div>
    <div class="wordmark">QUILLSTONE CHIEF</div>
    <blockquote class="quote">
      <p class="quote__text">“The Fastest Way To Success<br>Is To Take Action”</p>
      <p class="quote__author">— Dorian Pelletta, Quillstone Chief</p>
    </blockquote>
    <div class="holder">
      <p class="holder__name">Dorian Pelletta</p>
      <p class="holder__title">The Quillstone Chief</p>
    </div>
    <div class="contact">
      <div class="contact__icons" aria-hidden="true">
        <svg viewBox="0 0 16 16"><path d="M1 6c0-2 3-3.5 7-3.5S15 4 15 6v1.5h-3.5V6H4.5v1.5H1zM4 8h8l2 6H2z"/><circle cx="8" cy="10.8" r="1.6" fill="#fff"/></svg>
        <svg viewBox="0 0 16 16"><rect x="1" y="3" width="14" height="10"/><path d="M1.5 3.5 8 9l6.5-5.5" stroke="#fff" stroke-width="1.3" fill="none"/></svg>
        <svg viewBox="0 0 16 16"><circle cx="8" cy="8" r="7"/><path d="M1 8h14M8 1c-3 3.5-3 10.5 0 14M8 1c3 3.5 3 10.5 0 14" stroke="#fff" stroke-width="1" fill="none"/></svg>
      </div>
      <p>619-555-0148</p>
      <p>Dorian@QuillstoneChief.example</p>
      <p>www.QuillstoneChief.example</p>
    </div>
    <div class="accent-band accent-band--bottom"></div>
  </section>

  <section class="card card--company" aria-label="Company card">
    <div class="wordmark">BRIGHTVALE MEDIA</div>
    <div class="services">
      <div class="services__group">
        <p>Advanced Website &amp; App Development</p>
        <p>Websites, Apps, Online Voucher Systems</p>
      </div>
      <div class="services__group">
        <p>Leading Edge Marketing Services</p>
        <p>SMS, VB, SMM, SEM,</p>
      </div>
    </div>
    <div class="address">
      <p>248 N. Larkmoor&nbsp; 3rd Floor,</p>
      <p>San Diego CA 92173</p>
      <p class="address__web">www.BrightvaleMedia.com</p>
    </div>
  </section>
</main>
</body>
</html>
```